Business Cards - Brightpath Horizon

need to design unique business card for my mortgage business. I need to design credit card style business card for my business or any unique idea that you might have

Target Market(s)

Home Loan customers

Industry/Entity Type

Mortgage Brokerage

Contact Information for Business Card

please design credit card style or very unique style business card

Colors

Designer to choose colors to be used in the design.

Requirements
Must have
• Name
• position
• Phone number
• fax number
• email address
• website address
• social media address
• All above fields will be provided once design in finalised

```html
<!DOCTYPE html>
<html lang="en">
<head>
<meta charset="utf-8">
<title>Brightpath Horizon – Business Cards</title>
<link rel="stylesheet" href="https://fonts.googleapis.com/css2?family=Crimson+Text&family=Open+Sans:wght@400&display=swap">
<style>
  :root {
    --backdrop: #222222;
    --card-white: #ffffff;
    --brand-blue: #0533c8;
    --brand-orange: #f08a16;
    --divider: #6f8fd6;
    --ink: #1d1d1d;
    --on-blue: #ffffff;
  }
  * { margin: 0; padding: 0; box-sizing: border-box; }
  html, body {
    width: 1200px; height: 900px; overflow: hidden;
    background: var(--backdrop);
  }
  .stage { position: relative; width: 1200px; height: 900px; }

  .card {
    position: absolute; top: 306px;
    width: 440px; height: 271px;
    border-radius: 12px;
    box-shadow: 2px 4px 8px rgba(0,0,0,0.45);
  }
  .card--front { left: 149px; background: var(--card-white); }
  .card--back  { left: 608px; background: var(--brand-blue); }

  .brand-name {
    font-family: "Crimson Text", serif;
    font-weight: 400;
    text-transform: uppercase;
    line-height: 1;
  }
  .card--front .brand-name {
    position: absolute; left: 34px; top: 100px; width: 176px;
    color: var(--brand-blue);
    font-size: 26px; letter-spacing: 1px;
  }
  .card--front .brand-name .line-2 { display: block; font-size: 40px; margin-top: 2px; }

  .divider {
    position: absolute; left: 235px; top: 87px;
    width: 1px; height: 97px; background: var(--divider);
  }

  .contact { position: absolute; left: 256px; top: 84px; }
  .contact__name {
    font-family: "Crimson Text", serif;
    color: var(--brand-orange);
    font-size: 16px; letter-spacing: 0.4px; line-height: 18px;
    text-transform: uppercase;
  }
  .contact__role {
    font-family: "Open Sans", sans-serif;
    color: var(--ink); font-size: 12px; line-height: 14px;
  }
  .contact__list { list-style: none; margin-top: 10px; }
  .contact__item {
    display: flex; align-items: center; gap: 6px;
    font-family: "Open Sans", sans-serif;
    color: var(--ink); font-size: 12px; line-height: 16px;
  }
  .contact__icon { width: 9px; height: 9px; flex: none; fill: var(--brand-orange); }

  .card--back .brand-name {
    position: absolute; left: 0; top: 108px; width: 100%;
    text-align: center; color: var(--on-blue);
    font-size: 30px; letter-spacing: 1.5px;
  }
  .card--back .brand-name .line-2 { display: block; font-size: 50px; margin-top: 2px; }

  .social {
    position: absolute; left: 118px; top: 230px; width: 204px;
    display: flex; align-items: center; gap: 6px;
  }
  .social__rule { flex: 1; height: 1px; background: var(--on-blue); }
  .social__badge { width: 19px; height: 19px; background: var(--on-blue); }
  .social__rule:first-child { margin-right: 6px; }
  .social__rule:last-child { margin-left: 6px; }
</style>
</head>
<body>
<main class="stage">
  <section class="card card--front" aria-label="Business card front">
    <h1 class="brand-name"><span>Brightpath</span><span class="line-2">Horizon</span></h1>
    <div class="divider"></div>
    <div class="contact">
      <p class="contact__name">Daniel Hartley</p>
      <p class="contact__role">Managing Director</p>
      <ul class="contact__list">
        <li class="contact__item">
          <svg class="contact__icon" viewBox="0 0 10 10" aria-hidden="true"><path d="M1 3 Q5 0 9 3 L8 5 L6.5 4 L6.5 3.5 Q5 3 3.5 3.5 L3.5 4 L2 5 Z M2 6 L8 6 L8.5 9 L1.5 9 Z"/></svg>
          (044)555018274
        </li>
        <li class="contact__item">
          <svg class="contact__icon" viewBox="0 0 10 10" aria-hidden="true"><path d="M2 0 H7 V3 H9 V10 H1 V3 H2 Z M3 1 V3 H6 V1 Z M3 5 V6 H7 V5 Z M3 7 V8 H7 V7 Z" fill-rule="evenodd"/></svg>
          (044)555018275
        </li>
        <li class="contact__item">
          <svg class="contact__icon" viewBox="0 0 10 10" aria-hidden="true"><path d="M0 2 H10 V8 H0 Z"/><path d="M0 2 L5 6 L10 2" fill="none" stroke="#fff" stroke-width="0.9"/></svg>
          info@brightpathhorizon.com
        </li>
        <li class="contact__item">
          <svg class="contact__icon" viewBox="0 0 10 10" aria-hidden="true"><circle cx="5" cy="5" r="4.8"/><path d="M5 0.5 V9.5 M0.5 5 H9.5 M5 0.5 Q2 5 5 9.5 M5 0.5 Q8 5 5 9.5" fill="none" stroke="#fff" stroke-width="0.7"/></svg>
          www.brightpathhorizon.com
        </li>
      </ul>
    </div>
  </section>

  <section class="card card--back" aria-label="Business card back">
    <h2 class="brand-name"><span>Brightpath</span><span class="line-2">Horizon</span></h2>
    <div class="social">
      <span class="social__rule"></span>
      <span class="social__badge" role="img" aria-label="Social network profile"></span>
      <span class="social__badge" role="img" aria-label="Social network profile"></span>
      <span class="social__badge" role="img" aria-label="Social network profile"></span>
      <span class="social__rule"></span>
    </div>
  </section>
</main>
</body>
</html>
```